Design a single page Shopify store web page

We are looking to have a page designed for a single page Shopify store with 2 products. We already have a basic structure that we like, though we are open to suggestions. We are looking for somebody to provide a design/color scheme that we can then implement using Shopify's templating system. We can handle the implementation(HTML / CSS / jS) as we already have 2 web developers on the team, but have not been able to find a design we liked.

The job would consist of providing a mockup (photoshop or otherwise) and any vector graphics you choose to create for the site (we can provide product photos and other images).

You can also look at http://brickdune.com.au for some of our design direction we have used so far

Target Market(s)

Young Australian Males (18 - 49)

Industry/Entity Type

Store

Number of Pages Required

1 page

Font styles to use
Serif
Sans Serif

Requirements
Must have
• Single Page Design
• E-commerce Product Purchase
• Manly (whatever interpretation of that you have)

```html
<!DOCTYPE html>
<html lang="en">
<head>
<meta charset="utf-8">
<title>Brick Dune – Underwear &amp; Socks Plans</title>
<link href="https://fonts.googleapis.com/css2?family=Mulish:wght@300;400;600;700&display=swap" rel="stylesheet">
<style>
:root{
  --navy:#0f1f2d;
  --navy-2:#132536;
  --slate:#3e6074;
  --sky:#1fc6ea;
  --sky-deep:#0b9fd6;
  --card:#1db3e4;
  --card-edge:#6fd3f2;
  --orange:#ff9e0d;
  --orange-deep:#f28a00;
  --ink:#14202b;
  --muted:#8a8f95;
  --rule:#e6e8ea;
  --white:#ffffff;
  --photo-skin:#c89a82;
  --photo-stripe:#3b3f4a;
}
*{box-sizing:border-box;margin:0;padding:0}
html,body{width:1200px;height:2329px;overflow:hidden;background:var(--white)}
body{font-family:"Mulish",sans-serif;color:var(--ink);position:relative}
.abs{position:absolute}

/* Header */
.site-header{position:absolute;left:0;top:0;width:1200px;height:123px;background:var(--navy)}
.brand{position:absolute;left:166px;top:38px;font-size:42px;font-weight:300;letter-spacing:3px;color:var(--white);line-height:48px}
.main-nav{position:absolute;right:326px;top:52px;display:flex;gap:27px;font-size:14px;line-height:18px;color:var(--white);letter-spacing:.2px;white-space:nowrap}
.signup{position:absolute;left:903px;top:45px;width:103px;height:33px;background:var(--sky);color:var(--white);font-size:13px;line-height:31px;text-align:center;border:1px solid #5fdaf5;white-space:nowrap}

/* Hero */
.hero{position:absolute;left:0;top:123px;width:1200px;height:493px;background:linear-gradient(180deg,var(--sky) 0%,var(--sky-deep) 100%);overflow:hidden}
.hero-title{position:absolute;left:169px;top:100px;font-size:46px;font-weight:600;color:var(--navy);line-height:52px}
.hero-sub{position:absolute;left:170px;top:154px;font-size:32px;font-weight:600;color:var(--white);line-height:38px}
.hero-copy{position:absolute;left:171px;top:203px;width:360px;font-size:11.5px;line-height:17px;color:#e8623a}
.btn-orange{position:absolute;background:var(--orange);color:var(--white);font-weight:700;text-align:center}
.hero-btn{left:169px;top:277px;width:124px;height:35px;font-size:14px;line-height:35px}
.hero-dots{position:absolute;left:168px;top:334px;display:flex;gap:4px}
.hero-dots span{width:10px;height:10px;border-radius:50%;background:var(--navy)}
.hero-dots span:first-child{background:var(--sky)}
.hero-photo{position:absolute;left:629px;top:0;width:364px;height:493px;background:linear-gradient(180deg,#2fc8ea 0%,var(--photo-skin) 25%,var(--photo-skin) 55%,var(--photo-stripe) 58%,var(--photo-stripe) 88%,var(--photo-skin) 90%,#28b3e0 100%);opacity:.9}

/* How it works */
.section-title{position:absolute;left:0;width:1200px;text-align:center;font-size:34px;font-weight:600;color:var(--ink)}
.lead{position:absolute;left:233px;width:734px;text-align:center;font-size:11.5px;line-height:20px;color:var(--muted)}
.step{position:absolute;width:240px;text-align:center}
.step-icon{width:146px;height:146px;margin:0 auto;border-radius:50%;background:var(--orange);display:flex;align-items:center;justify-content:center}
.step-icon svg{display:block}
.step h3{font-size:20px;font-weight:600;margin-top:22px;color:var(--ink)}
.step p{font-size:11px;line-height:18.5px;color:var(--muted);margin-top:6px}

/* Plans */
.plans{position:absolute;left:0;top:1142px;width:1200px;height:457px;background:linear-gradient(180deg,var(--slate) 0%,var(--navy-2) 100%)}
.plans .section-title{color:var(--white);top:44px}
.plan-card{position:absolute;top:120px;width:391px;height:183px;background:var(--card);border:2px solid var(--card-edge)}
.plan-photo{position:absolute;left:21px;top:21px;width:160px;height:130px;border:3px solid var(--white)}
.plan-name{position:absolute;left:194px;top:18px;font-size:23px;font-weight:600;color:var(--white)}
.plan-copy{position:absolute;left:196px;top:50px;width:180px;font-size:11px;line-height:17px;color:var(--white)}
.plan-price{position:absolute;left:198px;top:120px;font-size:25px;color:var(--white)}
.plan-buy{position:absolute;left:258px;top:120px;width:90px;height:32px;background:#0f2a3a;color:var(--white);font-size:14px;font-weight:600;line-height:32px;text-align:center;letter-spacing:.5px}
.perks{position:absolute;top:354px;left:0;width:1200px;display:flex;justify-content:center;gap:26px;color:var(--white);font-size:16px}
.perk{display:flex;align-items:center;gap:11px}
.perk svg{flex:none}

/* FAQ */
.faq-item{position:absolute;width:420px}
.faq-q{font-size:20px;color:#4a5560;font-weight:400}
.faq-q b{color:var(--sky-deep);font-weight:600;margin-right:6px}
.faq-a{position:relative;padding-left:30px;margin-top:9px;font-size:11px;line-height:18.5px;color:var(--muted)}
.faq-a b{position:absolute;left:0;top:-2px;font-size:19px;color:var(--orange);font-weight:600}
.faq-rule{position:absolute;left:168px;width:864px;height:1px;background:var(--rule)}

/* Footer */
.site-footer{position:absolute;left:0;top:2196px;width:1200px;height:133px;background:var(--navy);color:var(--white)}
.footer-links{position:absolute;left:173px;top:41px;font-size:15px}
.copyright{position:absolute;left:173px;top:72px;font-size:10px;color:#aab4bc}
.contact{position:absolute;left:517px;top:42px;font-size:14px;display:flex;align-items:center;gap:8px}
.social{position:absolute;left:720px;top:38px;display:flex;gap:12px}
.social span{width:30px;height:30px}
.payments{position:absolute;left:903px;top:41px;display:flex;gap:8px}
.payments span{width:37px;height:23px;border-radius:3px}
</style>
</head>
<body>

<header class="site-header">
  <div class="brand">BRICK DUNE</div>
  <nav class="main-nav"><span>ABOUT</span><span>HOW IT WORKS</span><span>PLANS</span><span>FAQ</span></nav>
  <div class="signup">Sign Up Now</div>
</header>

<section class="hero">
  <h1 class="hero-title">Automate your Life</h1>
  <h2 class="hero-sub">New Underwear &amp; Socks</h2>
  <p class="hero-copy">Lorem ipsum dolor sit amet consectetuer adipiscing elit Nam cursus. Morbi ut mi Nullam enim leo egestas id condimentum at</p>
  <div class="btn-orange hero-btn">VIEW MORE</div>
  <div class="hero-dots"><span></span><span></span><span></span><span></span></div>
  <div class="hero-photo" role="img" aria-label="Photo of a fit man wearing striped trunks, shown from the torso down"></div>
</section>

<section class="how-it-works">
  <h2 class="section-title" style="top:685px">How it Works</h2>
  <p class="lead" style="top:732px">Vivamus porttitor g purus nisi eleifend libero a tempus libero lectus feugiat felis Morbi diam mauris viverra in gravida eu mattis in ante Morbi eget arcu Morbi porta libero id ullamcorper nonummy nibh ligula pulvinar metus eget consectetuer augue nisi quis lacus Ut</p>

  <svg class="abs" style="left:360px;top:810px" width="470" height="110" viewBox="0 0 470 110" fill="none" stroke="#e4e6e8" stroke-width="3">
    <path d="M0 50 C60 5 150 5 210 45"/>
    <path d="M310 80 C360 105 420 100 470 70"/>
  </svg>

  <div class="step" style="left:176px;top:805px">
    <div class="step-icon">
      <svg width="66" height="72" viewBox="0 0 66 72" fill="none" stroke="#fff" stroke-width="3.5" stroke-linejoin="round">
        <rect x="10" y="8" width="44" height="58" rx="3"/><rect x="22" y="3" width="20" height="10" rx="2"/>
        <path d="M19 26h26M19 36h26M19 46h14"/><path d="M36 55l6 6 12-14"/>
      </svg>
    </div>
    <h3>Choose a Plan</h3>
    <p>Vivamus porttitor purus nisi eleifend libero a tempus libero lectus feugiat felis Morbi diam mauris viverra in gravida eu matti</p>
  </div>

  <div class="step" style="left:473px;top:805px">
    <div class="step-icon">
      <svg width="72" height="70" viewBox="0 0 72 70" fill="none" stroke="#fff" stroke-width="3.5" stroke-linejoin="round">
        <rect x="4" y="10" width="56" height="48" rx="3"/><path d="M4 22h56M16 4v12M48 4v12"/>
        <path d="M14 32h4M24 32h4M34 32h4M44 32h4M14 42h4M24 42h4M34 42h4"/>
        <circle cx="56" cy="54" r="12" fill="#ff9e0d"/><path d="M56 48v6h5"/>
      </svg>
    </div>
    <h3>Choose How Often</h3>
    <p>Vivamus porttitor purus nisi eleifend libero a tempus libero lectus feugiat felis Morbi diam mauris viverra in gravida eu matti</p>
  </div>

  <div class="step" style="left:769px;top:805px">
    <div class="step-icon">
      <svg width="72" height="66" viewBox="0 0 72 66" fill="#fff">
        <path d="M6 22 L36 8 L66 22 L36 36 Z"/><path d="M6 26 L34 40 V62 L6 48 Z"/><path d="M66 26 L38 40 V62 L66 48 Z"/>
      </svg>
    </div>
    <h3>Get Your Pack</h3>
    <p>Vivamus porttitor purus nisi eleifend libero a tempus libero lectus feugiat felis Morbi diam mauris viverra in gravida eu matti</p>
  </div>
</section>

<section class="plans">
  <h2 class="section-title">Plans</h2>

  <article class="plan-card" style="left:191px">
    <div class="plan-photo" role="img" aria-label="Product photo of red checked boxer shorts worn by a model" style="background:linear-gradient(180deg,#e6ddd6 0%,#c89a82 40%,#b3283a 55%,#8f1d2c 80%,#e9e4e0 100%)"></div>
    <h3 class="plan-name">Comfort</h3>
    <p class="plan-copy">Mauris vel lacus vitae felis vestibulum volutpat Etiam est nunc in trimperdiet ac</p>
    <div class="plan-price">$30</div>
    <div class="plan-buy">GET IT!</div>
  </article>

  <article class="plan-card" style="left:594px">
    <div class="plan-photo" role="img" aria-label="Product photo of a man in red briefs relaxing outdoors under a blue sky" style="background:linear-gradient(180deg,#7fb4de 0%,#a9cde8 40%,#c89a82 60%,#a8323a 75%,#d9d4cc 100%)"></div>
    <h3 class="plan-name">Style</h3>
    <p class="plan-copy">Mauris vel lacus vitae felis vestibulum volutpat Etiam est nunc in trimperdiet ac</p>
    <div class="plan-price">$30</div>
    <div class="plan-buy">GET IT!</div>
  </article>

  <div class="perks">
    <div class="perk"><svg width="30" height="30" viewBox="0 0 30 30"><circle cx="15" cy="15" r="15" fill="#ff9e0d"/><path d="M8 15l5 5 9-10" fill="none" stroke="#fff" stroke-width="3"/></svg>Free Shipping</div>
    <div class="perk"><svg width="30" height="30" viewBox="0 0 30 30"><circle cx="15" cy="15" r="15" fill="#ff9e0d"/><path d="M8 15l5 5 9-10" fill="none" stroke="#fff" stroke-width="3"/></svg>Easy Returns</div>
    <div class="perk"><svg width="30" height="30" viewBox="0 0 30 30"><circle cx="15" cy="15" r="15" fill="#ff9e0d"/><path d="M8 15l5 5 9-10" fill="none" stroke="#fff" stroke-width="3"/></svg>Cancel Whenever</div>
    <div class="perk"><svg width="30" height="30" viewBox="0 0 30 30"><circle cx="15" cy="15" r="15" fill="#ff9e0d"/><path d="M8 15l5 5 9-10" fill="none" stroke="#fff" stroke-width="3"/></svg>Satisfaction Guaranteed</div>
  </div>
</section>

<section class="faq">
  <h2 class="section-title" style="top:1638px">FAQ</h2>

  <div class="faq-item" style="left:182px;top:1722px">
    <p class="faq-q"><b>Q:</b>Mauris vel lacus vitae felis vestibulum?</p>
    <p class="faq-a"><b>A:</b>Etiam est nunc venenatis in tristique eu imperdiet ac nisl Cum sociis natoque penatibus et magnis dis parturient montes nascetur ridiculus mus In iaculis facilisis massa Etiam eu urna Sed porta Suspendisse quam leo molestie sed luctus quis feugiat in pede Fusce</p>
  </div>
  <div class="faq-item" style="left:624px;top:1722px">
    <p class="faq-q"><b>Q:</b>Cum sociis natoque penatibus ?</p>
    <p class="faq-a"><b>A:</b>Etiam est nunc venenatis in tristique eu imperdiet ac nisl Cum sociis natoque penatibus et magnis dis parturient montes nascetur ridiculus mus In iaculis facilisis massa Etiam eu urna Sed porta Suspendisse quam leo molestie sed luctus quis feugiat in pede Fusce</p>
  </div>

  <div class="faq-rule" style="top:1858px"></div>

  <div class="faq-item" style="left:182px;top:1883px">
    <p class="faq-q"><b>Q:</b>Tempor cursus neque consectetuer?</p>
    <p class="faq-a"><b>A:</b>Etiam est nunc venenatis in tristique eu imperdiet ac nisl Cum sociis natoque penatibus et magnis dis parturient montes nascetur ridiculus mus In iaculis facilisis massa Etiam eu urna Sed porta Suspe</p>
  </div>
  <div class="faq-item" style="left:624px;top:1883px">
    <p class="faq-q"><b>Q:</b>Etiam est nunc venenatis in tristique ?</p>
    <p class="faq-a"><b>A:</b>Etiam est nunc venenatis in tristique eu imperdiet ac nisl Cum sociis natoque penatibus et magnis dis parturient montes nascetur ridiculus mus In iaculis facilisis massa Etiam eu u</p>
  </div>

  <div class="faq-rule" style="top:2002px"></div>

  <div class="faq-item" style="left:182px;top:2027px">
    <p class="faq-q"><b>Q:</b>Nunc porta convallis pede?</p>
    <p class="faq-a"><b>A:</b>Etiam est nunc venenatis in tristique eu imperdiet ac nisl Cum sociis natoque penatibus et magnis dis parturient montes nascetur ridiculus mus In iaculis facilisis massa Etiam eu urna Sed porta Suspendisse quam leo molestie sed luctus quis feugiat in pede Fusce</p>
  </div>
  <div class="faq-item" style="left:624px;top:2027px">
    <p class="faq-q"><b>Q:</b>Praesent elementum elit tellus ?</p>
    <p class="faq-a"><b>A:</b>Etiam est nunc venenatis in tristique eu imperdiet ac nisl Cum sociis natoque penatibus et magnis dis parturient montes nascetur ridiculus mus In iaculis facilisis massa Etiam eu urna Sed porta Suspendisse quam leo molestie sed luctus quis feugiat in pede Fusce</p>
  </div>
</section>

<footer class="site-footer">
  <div class="footer-links">Return &nbsp;|&nbsp; Payment &nbsp;|&nbsp; Term &nbsp;|&nbsp; Privacy</div>
  <div class="copyright">© 2014 Company Name &nbsp;All right reserved &nbsp;Term of Use</div>
  <div class="contact">
    <svg width="16" height="13" viewBox="0 0 16 13" fill="none" stroke="#fff" stroke-width="1.5"><rect x="1" y="1" width="14" height="11"/><path d="M1 1l7 6 7-6"/></svg>
    holla@brickdune.com.au
  </div>
  <div class="social">
    <span style="background:#3b5a9a"></span>
    <span style="background:#2aa9e0"></span>
    <span style="background:#3d5470"></span>
    <span style="background:#a8765a"></span>
  </div>
  <div class="payments">
    <span style="background:#6fb6e0"></span>
    <span style="background:#f2a824"></span>
    <span style="background:#5a6fb0"></span>
  </div>
</footer>

</body>
</html>
```